Local Flower Farm Needs Business Card Design

I need business cards designed for a flower farm based in Eudora, Kansas.
Business Info:
We are a local cut flower farm located in Eudora, Kansas, founded by Corinne Haldwick. What started as a passion for agriculture and search for more joy in daily life has blossomed into a small business dedicated to providing the community with beautiful, fresh, and sustainable flowers. We specialize in local, seasonal blooms, ensuring that every petal reflects the care and dedication we pour into our craft. Our mission is to deliver the highest quality flowers directly to our customers through local farmers markets and to florists who share our commitment to sustainability. Join us in celebrating the beauty of nature, one bloom at a time!
Contact Details:
Corinne Haldwick
Owner
Phone 913-555-0147
Facebook: Rosalind Thorpe Gardens
Instagram: @RosalindThorpeGardens
Website: RosalindThorpeGardens.example
Target Market(s)
Wholesale to Florists and Direct to Consumer via Farmers Market
Industry/Entity Type
Florist, Farm
Contact Information for Business Card
Name, Contact Info, Logo
Look and feel
Each slider illustrates characteristics of the customer's brand and the style your logo design should communicate.

```html
<!DOCTYPE html>
<html lang="en">
<head>
<meta charset="utf-8">
<title>Rosalind Thorpe Gardens — Business Card</title>
<link rel="stylesheet" href="https://fonts.googleapis.com/css2?family=Libre+Baskerville:wght@400;700&display=swap">
<style>
  :root {
    --stage: #1a1c1d;
    --card-white: #ffffff;
    --card-shade: #ececec;
    --teal-deep: #0f2a2f;
    --teal-mid: #1d3a3f;
    --ink: #0f2a2f;
    --text: #1b1b1b;
    --light: #e9eceb;
  }
  * { box-sizing: border-box; margin: 0; padding: 0; }
  html, body { width: 1200px; height: 963px; overflow: hidden; }
  body {
    background: var(--stage);
    font-family: "Libre Baskerville", "Times New Roman", serif;
    position: relative;
  }
  .card {
    position: absolute;
    left: 250px;
    width: 700px;
    height: 400px;
    border-radius: 28px;
    overflow: hidden;
  }
  .card--front {
    top: 50px;
    background: linear-gradient(135deg, var(--card-shade) 0%, var(--card-white) 45%);
  }
  .card--back {
    top: 513px;
    background: radial-gradient(ellipse at 50% 55%, var(--teal-mid) 0%, var(--teal-deep) 80%);
  }
  .identity {
    position: absolute;
    left: 175px;
    top: 58px;
  }
  .identity__name {
    font-size: 30px;
    font-weight: 700;
    color: var(--ink);
    letter-spacing: -0.3px;
  }
  .identity__role {
    font-size: 15px;
    color: var(--text);
    margin-top: 2px;
  }
  .contact {
    position: absolute;
    left: 62px;
    top: 190px;
    list-style: none;
  }
  .contact__item {
    display: flex;
    align-items: center;
    gap: 9px;
    font-size: 17px;
    color: var(--text);
    line-height: 30px;
  }
  .contact__icon { width: 16px; height: 16px; flex: none; }
  .contact__dot {
    width: 14px; height: 14px; border-radius: 3px; flex: none;
    background: var(--ink);
    margin: 0 1px;
  }
  .badge {
    position: absolute;
    border-radius: 50%;
    display: flex;
    align-items: center;
    justify-content: center;
    text-align: center;
  }
  .badge--front {
    width: 400px; height: 400px;
    right: -150px; bottom: -170px;
    border: 1.5px solid var(--ink);
  }
  .badge--front .badge__name {
    color: var(--ink);
    transform: translate(-70px, -70px);
  }
  .badge--back {
    width: 300px; height: 300px;
    left: 200px; top: 50px;
    border: 1.5px solid var(--light);
  }
  .badge--back .badge__name { color: var(--light); }
  .badge__name {
    font-size: 21px;
    font-weight: 400;
    letter-spacing: 4px;
    text-transform: uppercase;
    line-height: 1.5;
  }
</style>
</head>
<body>
  <section class="card card--front" aria-label="Business card front">
    <div class="identity">
      <h1 class="identity__name">Corinne Haldwick</h1>
      <p class="identity__role">Owner</p>
    </div>
    <ul class="contact">
      <li class="contact__item">
        <svg class="contact__icon" viewBox="0 0 16 16"><path fill="#1b1b1b" d="M4 1.5l2.2 3-1.4 1.6c.8 1.8 2.3 3.3 4.1 4.1l1.6-1.4 3 2.2-1.3 2.5C7 13.3 2.7 9 1.5 3z"/></svg>
        <span>913-555-0147</span>
      </li>
      <li class="contact__item">
        <svg class="contact__icon" viewBox="0 0 16 16" fill="none" stroke="#1b1b1b" stroke-width="1.4"><circle cx="8" cy="8" r="6.5"/><ellipse cx="8" cy="8" rx="3" ry="6.5"/><path d="M1.5 8h13"/></svg>
        <span>RosalindThorpeGardens.example</span>
      </li>
      <li class="contact__item">
        <span class="contact__dot"></span>
        <span>Rosalind Thorpe Gardens</span>
      </li>
      <li class="contact__item">
        <span class="contact__dot"></span>
        <span>@RosalindThorpeGardens</span>
      </li>
    </ul>
    <div class="badge badge--front">
      <span class="badge__name">Rosalind<br>Thorpe<br>Gardens</span>
    </div>
  </section>

  <section class="card card--back" aria-label="Business card back">
    <div class="badge badge--back">
      <span class="badge__name">Rosalind<br>Thorpe<br>Gardens</span>
    </div>
  </section>
</body>
</html>
```